Corvane Freight Company Business Card Design

We are a company that delivers natural saltwater (from the ocean) to aquarium companies, restaurants and home marine tanks. I would like a new business card to suit.

Must include Name, company name, abn, contact number and website as well as logo (see attached).

Looking for a design that stands out, has a clean but unique appearance.

Double and single sided entries welcome

Business

• Logo

```html
<!DOCTYPE html>
<html lang="en">
<head>
<meta charset="utf-8">
<title>Corvane Freight Company Business Card</title>
<link rel="stylesheet" href="https://fonts.googleapis.com/css2?family=Source+Sans+3:wght@400;600;700&display=swap">
<style>
  :root {
    --stage: #111214;
    --card-white: #ffffff;
    --ocean-blue: #0a5cad;
    --sky-blue: #1f8fd8;
    --foam-blue: #55c6f0;
    --ink-dark: #1c1c1e;
    --text-blue: #1f6cbd;
    --divider: #d4d8de;
  }
  * { box-sizing: border-box; margin: 0; padding: 0; }
  html, body {
    width: 1200px;
    height: 420px;
    overflow: hidden;
    background: var(--stage);
    font-family: "Source Sans 3", "Myriad Pro", Arial, sans-serif;
  }
  .canvas {
    position: relative;
    width: 1200px;
    height: 420px;
  }
  .card {
    position: absolute;
    top: 65px;
    width: 516px;
    height: 293px;
    border-radius: 22px;
    overflow: hidden;
  }
  .card-front {
    left: 69px;
    background: var(--card-white);
  }
  .card-back {
    left: 620px;
    background: var(--ocean-blue);
    border: 1px solid #9fb9d6;
    display: flex;
    align-items: center;
    justify-content: center;
  }
  .front-wave {
    position: absolute;
    left: 0;
    bottom: 0;
    width: 516px;
    height: 293px;
  }
  .front-wordmark {
    position: absolute;
    left: 38px;
    top: 95px;
    width: 280px;
    color: var(--sky-blue);
    font-weight: 400;
    font-size: 34px;
    line-height: 1.0;
    letter-spacing: -0.5px;
  }
  .front-divider {
    position: absolute;
    left: 333px;
    top: 46px;
    width: 1px;
    height: 168px;
    background: var(--divider);
  }
  .contact-block {
    position: absolute;
    left: 352px;
    top: 71px;
    color: var(--text-blue);
    font-size: 13px;
    line-height: 18px;
  }
  .contact-address { margin-bottom: 28px; }
  .contact-line {
    display: flex;
    align-items: center;
    gap: 6px;
  }
  .contact-line svg { width: 10px; height: 10px; flex: none; }
  .contact-abn { margin-top: 22px; }
  .holder-name {
    position: absolute;
    left: 38px;
    bottom: 21px;
    color: var(--card-white);
    font-size: 16px;
  }
  .holder-name strong { font-weight: 700; }
  .holder-name span { font-weight: 400; }
  .back-wordmark {
    width: 400px;
    text-align: center;
    color: var(--card-white);
    font-weight: 400;
    font-size: 46px;
    line-height: 1.05;
    letter-spacing: -0.5px;
  }
</style>
</head>
<body>
<main class="canvas">
  <section class="card card-front" aria-label="Business card front">
    <svg class="front-wave" viewBox="0 0 516 293" aria-hidden="true">
      <path d="M0,212 C140,216 320,268 516,248 L516,293 L0,293 Z" fill="var(--ocean-blue)"/>
      <path d="M0,214 C150,218 330,270 516,252 L516,258 C330,278 150,226 0,220 Z" fill="var(--ink-dark)"/>
      <path d="M120,214 C240,224 360,258 516,242 L516,247 C360,264 240,230 120,217 Z" fill="var(--foam-blue)"/>
    </svg>
    <div class="front-wordmark">Corvane Freight Company</div>
    <div class="front-divider"></div>
    <div class="contact-block">
      <p class="contact-address">Street Name, City Name<br>State, Zip Code</p>
      <p class="contact-line">
        <svg viewBox="0 0 10 10" aria-hidden="true"><circle cx="5" cy="5" r="4.3" fill="none" stroke="currentColor" stroke-width="1"/><path d="M3.3,2.6 L4.3,2.6 L4.6,4 L4,4.5 C4.4,5.3 4.8,5.7 5.5,6 L6,5.4 L7.4,5.7 L7.4,6.7 C5,7 3,5 3.3,2.6 Z" fill="currentColor"/></svg>
        123-456-7892
      </p>
      <p class="contact-line">
        <svg viewBox="0 0 10 10" aria-hidden="true"><circle cx="5" cy="5" r="4.3" fill="none" stroke="currentColor" stroke-width="1"/><ellipse cx="5" cy="5" rx="1.9" ry="4.3" fill="none" stroke="currentColor" stroke-width="0.8"/><path d="M0.7,5 H9.3" stroke="currentColor" stroke-width="0.8"/></svg>
        www.corvanefreight.com
      </p>
      <p class="contact-abn">ABN: 123456789</p>
    </div>
    <p class="holder-name"><strong>Your Name,</strong> <span>Title</span></p>
  </section>

  <section class="card card-back" aria-label="Business card back">
    <div class="back-wordmark">Corvane Freight Company</div>
  </section>
</main>
</body>
</html>
```